Aquatic View

We need a web design for a new window cleaning company name Tidewell Glass Care. We are located in Grand Cayman, Cayman Islands. We are a small company, a team of husband and wife. Our services include residencial interior and exterior window cleaning and commercial. Extra services such as ceiling fans cleaning, mirrors, high dusting. Home cleaning services. Power washing. Explaining the service. We want a modern, beachy style with aquatic colors. We want to use our domain name "tidewellglasscare.ky". We want to portray a clean, modern and professional design.

Target Market(s)

Big Home owners

Industry/Entity Type

Cleaning Service

Contact Information for Business Card

Company Name: Tidewell Glass Care
Name: Desmond Farrowby owner/manager
Phone: 345-9170452
Email: desmond@tidewellglasscare.ky
Website: tidewellglasscare.ky
Address: P.O.Box 2486 GT, George Town, Grand Cayman KY1-1203 Cayman Islands

Number of Pages Required

2 page

Font styles to use
Sans Serif

Colors
0592cd
0455a3
33a6d7
85cae6
cadf82
abd036
fbf289

Requirements
Nice to have
• Pictures of an ocean view and palm trees from clear windows.
• https://quorvantel.com/bidlinker/
• Use the above for "free estimate".

```html
<!DOCTYPE html>
<html lang="en">
<head>
<meta charset="utf-8">
<title>Tidewell Glass Care</title>
<link href="https://fonts.googleapis.com/css2?family=Roboto+Condensed:wght@400;700&family=Roboto:wght@400;500&display=swap" rel="stylesheet">
<style>
:root{
  --blue-deep:#0455a3;
  --blue:#0592cd;
  --blue-mid:#33a6d7;
  --blue-light:#85cae6;
  --lime:#abd036;
  --lime-soft:#cadf82;
  --ink:#1d2b3a;
  --text:#6b6b6b;
  --panel:#f3f3f3;
  --white:#ffffff;
}
*{box-sizing:border-box;margin:0;padding:0}
html,body{width:874px;height:1200px;overflow:hidden}
body{
  position:relative;
  font-family:"Roboto",Arial,sans-serif;
  background:linear-gradient(160deg,#d6ecf8 0%,#b5dbf1 40%,#9fcdeb 100%);
  color:var(--text);
}
.heading{font-family:"Roboto Condensed",Arial Narrow,sans-serif;color:var(--blue-deep);font-weight:400}
.header{position:absolute;left:0;top:0;width:874px;height:79px}
.brand{position:absolute;left:96px;top:28px;display:flex;align-items:center;gap:7px}
.brand-dot{width:16px;height:16px;border-radius:50%;background:var(--blue-deep)}
.brand-name{font-family:"Roboto Condensed",sans-serif;font-weight:700;font-size:12px;color:var(--blue-deep);letter-spacing:.5px}
.contact{position:absolute;right:141px;top:23px;text-align:right;font-family:"Roboto Condensed",sans-serif;white-space:nowrap}
.contact-label{font-size:11.5px;color:var(--ink)}
.contact-phone{font-size:14px;color:var(--blue-deep);margin-top:2px}
.contact-icon{position:absolute;left:745px;top:22px}
.nav{position:absolute;left:86px;top:79px;width:701px;height:43px;background:var(--blue-deep);display:flex}
.nav a{display:flex;align-items:center;font-size:9.6px;color:var(--white);text-decoration:none;padding:0 25px;border-right:1px solid rgba(255,255,255,.15);height:100%}
.nav a.active{background:var(--lime);width:78px;padding-left:24px}
.page{position:absolute;left:86px;top:122px;width:701px;height:980px;background:var(--white)}
.slider{position:absolute;left:10px;top:10px;width:681px;height:326px}
.slide-photo{position:absolute;inset:0;background:linear-gradient(90deg,#6a5540 0%,#7fa7c9 18%,#9ad0ee 45%,#3a8b4a 62%,#c59a5a 88%,#7a5a38 100%)}
.caption{position:absolute;left:0;bottom:0;width:100%;height:68px;background:rgba(4,85,163,.92);padding:16px 15px;color:var(--white)}
.caption h2{font-family:"Roboto Condensed",sans-serif;font-weight:400;font-size:14px}
.caption p{font-family:"Roboto Condensed",sans-serif;font-size:12.2px;margin-top:4px}
.arrow{position:absolute;top:139px;width:48px;height:48px;border-radius:50%;background:var(--white)}
.arrow.prev{left:-24px}.arrow.next{right:-24px}
.arrow svg{position:absolute;top:17px}
.arrow.prev svg{left:27px}.arrow.next svg{left:13px}
.welcome{position:absolute;left:0;top:362px;width:701px;text-align:center}
.welcome h1{font-size:18px}
.welcome p{font-size:8.2px;line-height:17px;margin:13px auto 0;width:590px}
.card{position:absolute;top:452px;width:197px;height:254px;border:1px solid #e2e2e2;text-align:center}
.card-photo{height:151px;border-radius:98px 98px 0 0;margin:-1px -1px 0}
.card h3{font-size:12.3px;margin-top:16px}
.card p{font-size:8.2px;line-height:17px;padding:3px 10px 0;text-align:justify;text-align-last:center}
.c1{left:22px}.c2{left:251px}.c3{left:483px}
.c1 .card-photo{background:linear-gradient(160deg,#c7c7c7,#d9b38a 55%,#a39a45)}
.c2 .card-photo{background:linear-gradient(160deg,#3fb08a,#5fa6c8 45%,#d9643a)}
.c3 .card-photo{background:linear-gradient(180deg,#2f7bc4,#78b9e6)}
.divider{position:absolute;left:10px;top:730px;width:681px;height:1px;background:#e6e6e6}
.about{position:absolute;left:12px;top:751px;width:400px}
.about h2{font-size:13.6px}
.about-photo{position:absolute;left:-2px;top:32px;width:134px;height:97px;background:linear-gradient(120deg,#3a4d6a,#d9dde3 50%,#e6cbb0)}
.about-body{margin:14px 7px 0 144px;font-size:8.2px;line-height:17.6px;text-align:justify}
.about-more{font-size:8.2px;line-height:17.6px;margin-top:8px;text-align:justify;width:400px;margin-left:-2px}
.read-more{display:inline-block;margin-top:7px;font-size:9.6px;font-style:italic;color:var(--lime);text-decoration:underline;margin-left:-2px}
.testimonial{position:absolute;left:429px;top:755px;width:262px;height:196px;background:var(--panel);padding:24px 19px}
.testimonial h2{font-size:13.6px}
.t-arrows{position:absolute;right:11px;top:25px}
.client{display:flex;align-items:center;margin-top:18px;gap:17px}
.client-photo{width:42px;height:42px;border-radius:50%;background:linear-gradient(135deg,#e9c8b0,#8a5a3e);border:2px solid var(--white)}
.client h3{font-size:13.6px}
.client span{font-size:9.6px;color:#555;display:block;margin-top:4px}
.testimonial p{font-size:8.2px;line-height:17.6px;margin-top:13px;text-align:justify}
.footer{position:absolute;left:86px;top:1102px;width:701px;height:40px;background:var(--blue-deep);color:var(--white);font-size:9.6px;padding:14px 16px}
.social{position:absolute;right:10px;top:6px;display:flex;gap:6px}
.social span{width:28px;height:28px;border-radius:50%;background:var(--blue-mid)}
</style>
</head>
<body>
<header class="header">
  <div class="brand"><span class="brand-dot"></span><span class="brand-name">TIDEWELL GLASS CARE</span></div>
  <div class="contact">
    <div class="contact-label">CONTACT US :</div>
    <div class="contact-phone">345-9170452</div>
  </div>
  <svg class="contact-icon" width="30" height="30" viewBox="0 0 30 30" aria-hidden="true">
    <circle cx="15" cy="15" r="13.5" fill="none" stroke="#1d2b3a" stroke-width="2"/>
    <path d="M10 9c1-1 2-1 3 1l1 2c0 1-1 1-1 2 1 2 2 3 4 4 1 0 1-1 2-1l2 1c2 1 2 2 1 3-2 2-5 1-8-2s-5-7-4-10z" fill="#1d2b3a"/>
  </svg>
</header>

<nav class="nav">
  <a class="active" href="#">HOME</a>
  <a href="#" style="padding:0 28px">ABOUT US</a>
  <a href="#" style="padding:0 28px">SERVICES</a>
  <a href="#" style="padding:0 30px">OUR BLOG</a>
  <a href="#" style="padding:0 28px">GALLERY</a>
  <a href="#" style="padding:0 27px">CONTACT US</a>
</nav>

<main class="page">
  <section class="slider">
    <div class="slide-photo" role="img" aria-label="Open window with curtains looking out on palm trees and a turquoise beach"></div>
    <div class="caption">
      <h2>TIDEWELL GLASS CARE</h2>
      <p>Perspiciatis unde omnis iste natus error sit voluptatem accusantium doloremque laudantium totam rem aperiam</p>
    </div>
    <div class="arrow prev"><svg width="9" height="14" viewBox="0 0 9 14"><path d="M8 1 2 7l6 6" fill="none" stroke="#abd036" stroke-width="2"/></svg></div>
    <div class="arrow next"><svg width="9" height="14" viewBox="0 0 9 14"><path d="m1 1 6 6-6 6" fill="none" stroke="#abd036" stroke-width="2"/></svg></div>
  </section>

  <section class="welcome">
    <h1 class="heading">WELCOME TO OUR TIDEWELL GLASS CARE</h1>
    <p>Lorem ipsum dolor sit amet, consectetur adipiscing elit, sed do eiusmod tempor incididunt ut labore et dolore magna aliqua ut enim ad minim veniam,<br>quis nostrud exercitation ullamco laboris nisi ut aliquip ex ea commodo consequat duis aute irure dolor in</p>
  </section>

  <article class="card c1">
    <div class="card-photo" role="img" aria-label="Hands wiping a ceiling fan blade with a cloth"></div>
    <h3 class="heading">CEILING FANS CLEANING</h3>
    <p>Lorem ipsum dolor sit amet, consectetur adipiscing elit sed do eiusmod tempor incididunt ut labore et dolore</p>
  </article>
  <article class="card c2">
    <div class="card-photo" role="img" aria-label="Gloved hands spraying and wiping a mirror"></div>
    <h3 class="heading">MIRRORS CLEANING</h3>
    <p>Lorem ipsum dolor sit amet, consectetur adipiscing elit sed do eiusmod tempor incididunt ut labore et dolore</p>
  </article>
  <article class="card c3">
    <div class="card-photo" role="img" aria-label="Squeegee clearing water from a window against blue sky"></div>
    <h3 class="heading">INTERIOR AND EXTERIOR</h3>
    <p>Lorem ipsum dolor sit amet, consectetur adipiscing elit sed do eiusmod tempor incididunt ut labore et dolore</p>
  </article>

  <div class="divider"></div>

  <section class="about">
    <h2 class="heading">ABOUT US</h2>
    <div class="about-photo" role="img" aria-label="Two cleaners washing windows in a bright room"></div>
    <p class="about-body">Lorem ipsum dolor sit amet, consectetur adipiscing elit, sed do eiusmod tempor incididunt ut labore et dolore magna aliqua ut enim ad minim veniam, quis nostrud exercitation ullamco laboris nisi ut aliquip Sed ut perspiciatis unde omnis iste natus error sit voluptatem accusantium doloremque laudantium, totam rem aperiam, eaque ipsa quae ab</p>
    <p class="about-more">Sed ut perspiciatis unde omnis iste natus error sit voluptatem accusantium doloremque laudantium, totam rem aperiam, eaque ipsa quae ab illo inventore veritatis et quasi.</p>
    <a class="read-more" href="#">READ MORE</a>
  </section>

  <aside class="testimonial">
    <h2 class="heading">CLIENT TESTIMONIAL</h2>
    <svg class="t-arrows" width="20" height="10" viewBox="0 0 20 10" aria-hidden="true"><path d="M5 1 1 5l4 4M15 1l4 4-4 4" fill="none" stroke="#abd036" stroke-width="1.5"/></svg>
    <div class="client">
      <div class="client-photo" role="img" aria-label="Client portrait"></div>
      <div><h3 class="heading">MARLA QUINTRELL,</h3><span>Client Details.</span></div>
    </div>
    <p>Lorem ipsum dolor sit amet, consectetur adipiscing elit, sed do eiusmod tempor incididunt ut labore et dolore magna aliqua ut enim ad minim veniam, quis nostrud exercitation ullamco laboris nisi ut aliquip</p>
  </aside>
</main>

<footer class="footer">
  Copyright © 2015 Tidewell Glass Care . All rights reserved.
  <div class="social"><span></span><span></span><span></span><span></span></div>
</footer>
</body>
</html>
```